Brightmill Data Works

Our company is about IT hardwares and IT solutions. IT hardware such as PC, RAMS, storage and servers. IT solutions such as project management, BA. We are also selling new technology too.

Target Market(s)

Consumer, Small to Medium Business, Corporate

Requirements
Must have
• The business card must have the following:
• Name:
• Title:
• Contact Number:
• Email address:
• Website:
• Color: Must match the logo color upgrade

```html
<!DOCTYPE html>
<html lang="en">
<head>
<meta charset="utf-8">
<title>Brightmill Data Works – Business Card</title>
<link rel="stylesheet" href="https://fonts.googleapis.com/css2?family=Titillium+Web:wght@400;600;700&display=swap">
<style>
  :root {
    --backdrop: #ebeae7;
    --card: #f3e0c8;
    --card-shade: #ecd5b9;
    --ink: #2f2f35;
    --accent: #d4862a;
    --muted: #55504a;
  }
  * { margin: 0; padding: 0; box-sizing: border-box; }
  html, body {
    width: 1200px; height: 997px; overflow: hidden;
    background: var(--backdrop);
    font-family: "Titillium Web", "Arial Narrow", sans-serif;
  }
  .canvas {
    width: 1200px; height: 997px;
    display: flex; align-items: center; justify-content: center; gap: 90px;
  }
  .card {
    position: relative;
    width: 360px; height: 600px;
    background: var(--card);
    box-shadow: 0 10px 30px rgba(0,0,0,0.12);
    overflow: hidden;
  }
  /* front side */
  .card-front .identity {
    position: absolute; left: 0; right: 0; top: 220px;
    display: flex; flex-direction: column; align-items: center; gap: 18px;
  }
  .brand-dot {
    width: 46px; height: 46px; border-radius: 50%;
    background: var(--accent);
  }
  .brand-name {
    color: var(--ink);
    font-weight: 700; font-size: 30px; line-height: 1.05;
    text-transform: uppercase; text-align: center; letter-spacing: 0.5px;
  }
  .card-front .website {
    position: absolute; left: 0; right: 0; bottom: 60px;
    text-align: center; color: var(--ink);
    font-size: 14px; letter-spacing: 3px;
  }
  /* back side */
  .back-tone {
    position: absolute; left: -60px; top: 300px;
    width: 300px; height: 260px; border-radius: 60px;
    background: var(--card-shade);
    transform: rotate(45deg);
  }
  .back-tone.upper {
    left: 200px; top: -160px; width: 240px; height: 240px;
  }
  .card-back .brand-dot {
    position: absolute; right: 44px; top: 70px;
    width: 40px; height: 40px;
  }
  .contact-block {
    position: absolute; left: 40px; bottom: 90px;
  }
  .person-name {
    color: var(--ink); font-weight: 700; font-size: 26px;
    text-transform: uppercase; line-height: 1.1;
  }
  .person-title {
    color: var(--accent); font-weight: 600; font-size: 14px;
    text-transform: uppercase; letter-spacing: 1px; margin-bottom: 14px;
  }
  .contact-list { list-style: none; }
  .contact-list li {
    display: flex; align-items: center; gap: 8px;
    color: var(--muted); font-size: 14px; line-height: 1.6;
  }
  .contact-list svg { width: 12px; height: 12px; fill: var(--ink); flex: none; }
</style>
</head>
<body>
<main class="canvas">
  <section class="card card-front">
    <div class="identity">
      <span class="brand-dot"></span>
      <h1 class="brand-name">Brightmill<br>Data Works</h1>
    </div>
    <p class="website">www.brightmilldata.com</p>
  </section>

  <section class="card card-back">
    <span class="back-tone"></span>
    <span class="back-tone upper"></span>
    <span class="brand-dot"></span>
    <div class="contact-block">
      <h2 class="person-name">Dana Whitlock</h2>
      <p class="person-title">CEO/Founder</p>
      <ul class="contact-list">
        <li>
          <svg viewBox="0 0 24 24" aria-hidden="true"><path d="M6.6 10.8a15.1 15.1 0 0 0 6.6 6.6l2.2-2.2a1 1 0 0 1 1-.25 11.4 11.4 0 0 0 3.6.57 1 1 0 0 1 1 1V20a1 1 0 0 1-1 1A17 17 0 0 1 3 4a1 1 0 0 1 1-1h3.5a1 1 0 0 1 1 1c0 1.25.2 2.45.57 3.6a1 1 0 0 1-.25 1z"/></svg>
          555 014 2290
        </li>
        <li>
          <svg viewBox="0 0 24 24" aria-hidden="true"><path d="M2 5h20v14H2z M3.5 6.5 12 13l8.5-6.5" fill="none" stroke="#2f2f35" stroke-width="2.5"/></svg>
          dana@brightmilldata.com
        </li>
        <li>
          <svg viewBox="0 0 24 24" aria-hidden="true"><circle cx="12" cy="12" r="10"/></svg>
          www.brightmilldata.com
        </li>
      </ul>
    </div>
  </section>
</main>
</body>
</html>
```